Brell Stone Company Business Cards

Front and Back Business Card - logo and text setup - cool design. I need workable photoshop or illustrator files so I can setup each employee card with design that is created
Updates

Hi everyone, thank you for the great entries. Please no more white and blue cards - there are so many already - black and silver only now please. thanks!

Target Market(s)

Construction Industry - Facility Managers

Industry/Entity Type

Construction

Contact Information for Business Card

I really like contemporary simplistic looks - clean neat....not opposed to seeing some black backrounds

Requirements
Must have
• Logo/website address with design on front only - www.brellstone-example.com (logo attached)
• Back:
• Name/Title/Company Address/Phone/email address
Nice to have
• Cool design
Should not have
• Nothing gimmicky like Fire or Water - since we are a Fire Protection company - it has all been done

```html
<!DOCTYPE html>
<html lang="en">
<head>
<meta charset="utf-8">
<title>Brell Stone Company – Business Cards</title>
<link rel="stylesheet" href="https://fonts.googleapis.com/css2?family=Open+Sans:wght@400;700;800&display=swap">
<style>
  :root {
    --backdrop: #c9cdd1;
    --card-black: #0c0c0c;
    --card-glow: #2a2a2a;
    --brand-red: #e8252b;
    --band-red: #d6232a;
    --brand-blue: #0a2aa0;
    --band-blue: #0726a0;
    --text-white: #ffffff;
    --rule-grey: #5a5a5a;
  }
  * { margin: 0; padding: 0; box-sizing: border-box; }
  html, body {
    width: 1200px; height: 1193px; overflow: hidden;
    background: var(--backdrop);
    font-family: "Open Sans", Arial, sans-serif;
  }
  .card {
    position: absolute;
    width: 1049px; height: 600px;
    border-radius: 52px;
    overflow: hidden;
    background:
      radial-gradient(ellipse 70% 60% at 50% 30%, var(--card-glow) 0%, var(--card-black) 70%);
    transform-origin: top left;
    transform: scale(0.8313);
    color: var(--text-white);
  }
  .card--contact { left: 73px; top: 76px; }
  .card--brand { left: 266px; top: 618px; }

  .card__band {
    position: absolute; left: 0; right: 0; bottom: 0; height: 105px;
    background: linear-gradient(to bottom, var(--band-red) 0%, var(--band-red) 35%, var(--band-blue) 75%, var(--band-blue) 100%);
  }

  .wordmark {
    position: absolute;
    display: flex; align-items: center; gap: 16px;
    font-weight: 800;
    color: var(--brand-red);
    white-space: nowrap;
    letter-spacing: -0.5px;
  }
  .wordmark__square { background: var(--brand-blue); flex: none; }

  .card--contact .wordmark { left: 104px; top: 240px; font-size: 40px; }
  .card--contact .wordmark__square { width: 34px; height: 34px; }

  .divider {
    position: absolute; left: 597px; top: 113px;
    width: 2px; height: 323px; background: var(--rule-grey);
  }
  .contact { position: absolute; left: 628px; top: 100px; }
  .contact__name { font-weight: 700; font-size: 33px; line-height: 44px; }
  .contact__title { font-size: 29px; line-height: 40px; }
  .contact__lines { list-style: none; margin-top: 24px; }
  .contact__lines li {
    display: flex; align-items: center; gap: 14px;
    font-size: 26px; height: 46px;
  }
  .contact__icon { width: 27px; height: 27px; flex: none; }
  .contact__address { margin-top: 16px; font-size: 28px; line-height: 40px; }

  .card--brand .wordmark {
    left: 0; right: 0; justify-content: center;
    top: 200px; font-size: 66px;
  }
  .card--brand .wordmark__square { width: 54px; height: 54px; }
  .card--brand .site {
    position: absolute; left: 0; right: 0; top: 372px;
    text-align: center; font-size: 32px; letter-spacing: 5px;
  }
</style>
</head>
<body>

<section class="card card--contact" aria-label="Business card, contact side">
  <div class="wordmark"><span class="wordmark__square"></span>Brell Stone Company</div>
  <div class="divider"></div>
  <div class="contact">
    <p class="contact__name">Dana Whitlock</p>
    <p class="contact__title">President</p>
    <ul class="contact__lines">
      <li>
        <svg class="contact__icon" viewBox="0 0 24 24" aria-hidden="true"><path fill="#e8252b" d="M6.6 10.8c1.4 2.8 3.8 5.1 6.6 6.6l2.2-2.2c.3-.3.7-.4 1-.2 1.1.4 2.3.6 3.6.6.6 0 1 .4 1 1V20c0 .6-.4 1-1 1C10.6 21 3 13.4 3 4c0-.6.4-1 1-1h3.5c.6 0 1 .4 1 1 0 1.3.2 2.5.6 3.6.1.3 0 .7-.2 1z"/></svg>
        (555) 014-2278
      </li>
      <li>
        <svg class="contact__icon" viewBox="0 0 24 24" aria-hidden="true"><rect x="2" y="5" width="20" height="14" fill="#e8252b"/><path d="M2 5l10 8 10-8M2 19l7-6M22 19l-7-6" stroke="#0c0c0c" stroke-width="1.6" fill="none"/></svg>
        info@brellstone-example.com
      </li>
      <li>
        <svg class="contact__icon" viewBox="0 0 24 24" aria-hidden="true"><g fill="none" stroke="#e8252b" stroke-width="1.8"><circle cx="12" cy="12" r="10"/><ellipse cx="12" cy="12" rx="4.5" ry="10"/><path d="M2 12h20M4 7h16M4 17h16"/></g></svg>
        www.brellstone-example.com
      </li>
    </ul>
    <p class="contact__address">48 Harbor Point Road<br>Fairview, NY 10990</p>
  </div>
  <div class="card__band" role="img" aria-label="Decorative red and blue band along the bottom edge"></div>
</section>

<section class="card card--brand" aria-label="Business card, brand side">
  <div class="wordmark"><span class="wordmark__square"></span>Brell Stone Company</div>
  <p class="site">www.brellstone-example.com</p>
  <div class="card__band" role="img" aria-label="Decorative red and blue band along the bottom edge"></div>
</section>

</body>
</html>
```